Popup Nightclub Grand Opening Flyer

We need to design a flyer for the grand opening of an upscale, exclusive nightclub called "Lantern". The design needs to be chic and exclusive. The background should be black and the text should primarily be white. We like minimalist designs.

Here is the text for the flyer
-
Velvetroll Atlanta Presents

Lantern (LOGO)

A Popup Nightclub Experience
For one night Only

Friday, October 18, 2013
Party begins at 9PM

INVITE ONLY

See invitation for location details
(Velvetroll Atlanta logo)

-
Examples we like

http://cdn4-x.pressfolio-example.com/sites/default/files/styles/image_content_width/hash/3b/fd/2468013579_4421_flyer.jpg?itok=K9rtQw2z

http://files.hubspace-example.net/files/8Hqq-Tr72WWE3kaRbTmcxP5QZK2F396J8nbRw4CKMHfdX2Y7qSEF-MqjxDoNrLY3QCyQJD7npjGaRq3k-Mhx6hqf3MDSWf8r3/2zenSaturdays.jpg

http://morvex-example.com/wp-content/uploads/siteskin/widgetkit/gallery/2zen/2zen-gen_qstay4-01.jpg

Hi All, one thing that we are seeing that we don't like is on over emphasis on the phrase "a popup nightclub experience" please don't make this the largest thing on the flyer

Target Market(s)

Target market is 25-35 year olds who are affluent (rich) and like luxury brands

Requirements
Must have
• Dark Background
Nice to have
• Velvetroll Logo on the bottom
Modern text that isn't curvy
Should not have
• Curved text

```html
<!DOCTYPE html>
<html lang="en">
<head>
<meta charset="utf-8">
<title>Lantern Popup Nightclub – Velvetroll Atlanta</title>
<link rel="stylesheet" href="https://fonts.googleapis.com/css2?family=Oswald:wght@300;400;600&family=Jost:wght@200;300;400&family=Open+Sans:wght@700;800&display=swap">
<style>
  :root {
    --flyer-black: #0b0b0b;
    --flyer-shadow: #1c1c1c;
    --ink-white: #f4f4f4;
    --ink-soft: #d9d9d9;
    --ink-dim: #9a9a9a;
    --ornament-tone: #262626;
  }
  html, body {
    margin: 0;
    padding: 0;
    width: 827px;
    height: 1200px;
    overflow: hidden;
    background: var(--flyer-black);
  }
  .flyer {
    position: relative;
    width: 827px;
    height: 1200px;
    background: radial-gradient(ellipse at 50% 58%, var(--flyer-shadow) 0%, var(--flyer-black) 62%);
    color: var(--ink-white);
    text-align: center;
  }
  .line {
    position: absolute;
    left: 0;
    right: 0;
    margin: 0;
    line-height: 1;
    white-space: nowrap;
  }
  .presenter {
    top: 78px;
    font-family: "Oswald", sans-serif;
    font-weight: 400;
    font-size: 48px;
    letter-spacing: 2px;
  }
  .presenter .city {
    font-family: "Jost", sans-serif;
    font-weight: 300;
    font-size: 26px;
    letter-spacing: 1px;
  }
  .presents {
    top: 128px;
    font-family: "Oswald", sans-serif;
    font-weight: 600;
    font-size: 58px;
    letter-spacing: 17px;
    padding-left: 17px;
  }
  .divider {
    position: absolute;
    left: 186px;
    width: 450px;
    border: 0;
    border-top: 2px dotted var(--ink-soft);
    margin: 0;
  }
  .divider.top { top: 208px; }
  .divider.mid { top: 812px; left: 160px; width: 505px; }
  .divider.low { top: 924px; left: 160px; width: 505px; }
  .venue-mark {
    position: absolute;
    top: 244px;
    left: 378px;
  }
  .venue-name {
    top: 330px;
    font-family: "Jost", sans-serif;
    font-weight: 300;
    font-size: 96px;
    letter-spacing: 10px;
    padding-left: 10px;
  }
  .headline {
    top: 488px;
    font-family: "Jost", sans-serif;
    font-weight: 200;
    font-size: 84px;
    letter-spacing: 6px;
    padding-left: 6px;
  }
  .night-club {
    top: 628px;
    font-family: "Jost", sans-serif;
    font-weight: 300;
    font-size: 44px;
    letter-spacing: 10px;
    padding-left: 10px;
  }
  .experience {
    top: 680px;
    font-family: "Open Sans", sans-serif;
    font-weight: 800;
    font-size: 60px;
    letter-spacing: 1px;
  }
  .one-night {
    top: 744px;
    font-family: "Open Sans", sans-serif;
    font-weight: 700;
    font-size: 32px;
    letter-spacing: 1px;
  }
  .date {
    top: 826px;
    font-family: "Oswald", sans-serif;
    font-weight: 600;
    font-size: 46px;
  }
  .start-time {
    top: 876px;
    font-family: "Oswald", sans-serif;
    font-weight: 300;
    font-size: 44px;
    letter-spacing: 1px;
  }
  .access-note {
    top: 976px;
    font-family: "Jost", sans-serif;
    font-weight: 400;
    font-size: 14px;
    letter-spacing: 0.5px;
    color: var(--ink-soft);
  }
  .host-mark {
    position: absolute;
    top: 1022px;
    left: 0;
    right: 0;
    display: flex;
    justify-content: center;
    align-items: center;
    gap: 18px;
  }
  .host-mark .square {
    width: 40px;
    height: 40px;
    border: 2px solid var(--ink-white);
    box-sizing: border-box;
  }
  .host-mark .host-name {
    font-family: "Oswald", sans-serif;
    font-weight: 400;
    font-size: 40px;
    letter-spacing: 3px;
    line-height: 1;
  }
  .ornament {
    position: absolute;
  }
  .ornament.left { left: 20px; top: 990px; width: 210px; height: 210px;
    background: radial-gradient(ellipse at 40% 60%, var(--ornament-tone) 0%, transparent 70%); }
  .ornament.right { right: 20px; top: 990px; width: 210px; height: 210px;
    background: radial-gradient(ellipse at 60% 60%, var(--ornament-tone) 0%, transparent 70%); }
  .ornament.base { left: 200px; right: 200px; top: 1130px; height: 70px;
    background: radial-gradient(ellipse at 50% 60%, var(--ornament-tone) 0%, transparent 72%); }
</style>
</head>
<body>
<main class="flyer">
  <p class="line presenter">VELVETROLL <span class="city">ATLANTA</span></p>
  <p class="line presents">PRESENTS</p>
  <hr class="divider top">

  <svg class="venue-mark" width="70" height="70" viewBox="0 0 70 70" aria-hidden="true">
    <circle cx="35" cy="35" r="31" fill="none" stroke="var(--ink-soft)" stroke-width="4"/>
  </svg>
  <h1 class="line venue-name">LANTERN</h1>

  <p class="line headline">A POPUP</p>
  <p class="line night-club">NIGHT CLUB</p>
  <p class="line experience">EXPERIENCE</p>
  <p class="line one-night">FOR ONE NIGHT ONLY</p>

  <hr class="divider mid">
  <p class="line date">FRIDAY, OCTOBER 18, 2013</p>
  <p class="line start-time">PARTY BEGINS AT 9PM</p>
  <hr class="divider low">

  <p class="line access-note">INVITE ONLY&nbsp;&nbsp;SEE INVITATION FOR LOCATION DETAILS</p>

  <div class="host-mark">
    <span class="square"></span>
    <span class="host-name">VELVETROLL ATLANTA</span>
  </div>

  <div class="ornament left" role="img" aria-label="Dark baroque flourish in the lower left corner"></div>
  <div class="ornament right" role="img" aria-label="Dark baroque flourish in the lower right corner"></div>
  <div class="ornament base" role="img" aria-label="Dark baroque scrollwork along the bottom edge"></div>
</main>
</body>
</html>
```